Design a business card
Business name: Harbourline Growth Advisory
Improving Business Profitibility

- An Overview of the Business & Service:

Business Performance Consulting

- The Target Market: Small to medium-sized business

- Design Specifics:
White card, blue ink, moon eclipse

No Logo

Target Market(s)

Small to medium-sized business

Font styles to use
Sans Serif

```html
<!DOCTYPE html>
<html lang="en">
<head>
<meta charset="utf-8">
<title>Harbourline Growth Advisory – Business Card</title>
<link href="https://fonts.googleapis.com/css2?family=Open+Sans:wght@400;600&family=Oswald:wght@400;500&display=swap" rel="stylesheet">
<style>
  :root {
    --backdrop: #3a3230;
    --card: #0c0c0d;
    --card-edge: #1a1a1c;
    --brand-blue: #1f5fb8;
    --silver: #d9d9db;
    --text-light: #c9c9cc;
    --text-dim: #8a8a8e;
    --rule: #4a4a4e;
  }
  * { box-sizing: border-box; margin: 0; padding: 0; }
  html, body {
    width: 1200px; height: 844px; overflow: hidden;
    background: var(--backdrop);
  }
  .stage {
    position: relative; width: 1200px; height: 844px;
    display: flex; align-items: center; justify-content: center; gap: 60px;
  }
  .card {
    position: relative;
    width: 520px; height: 297px;
    background: var(--card);
    border: 1px solid var(--card-edge);
    box-shadow: 0 18px 40px rgba(0,0,0,.45);
    overflow: hidden;
  }

  /* Contact side */
  .card--contact .brand-block {
    position: absolute; left: 34px; top: 0; bottom: 0; width: 190px;
    display: flex; align-items: center; gap: 12px;
  }
  .brand-dot {
    width: 18px; height: 18px; border-radius: 50%;
    background: var(--brand-blue); flex: none;
  }
  .brand-name {
    font-family: 'Oswald', sans-serif; font-weight: 500;
    color: var(--brand-blue); font-size: 24px; line-height: 1.1;
    text-transform: uppercase; letter-spacing: .5px;
  }
  .divider {
    position: absolute; left: 240px; top: 70px; bottom: 60px;
    width: 1px; background: var(--rule);
  }
  .contact {
    position: absolute; left: 262px; top: 72px;
    font-family: 'Open Sans', sans-serif; color: var(--text-light);
    font-size: 14px; line-height: 1.35;
  }
  .contact .person {
    font-family: 'Oswald', sans-serif; font-weight: 500;
    color: var(--brand-blue); font-size: 17px; text-transform: uppercase;
    letter-spacing: .3px;
  }
  .contact .role { margin-bottom: 2px; }
  .contact ul { list-style: none; }
  .contact li { display: flex; align-items: center; gap: 8px; }
  .contact li svg { width: 11px; height: 11px; fill: var(--text-dim); flex: none; }
  .contact .address { margin-top: 6px; }

  /* Front side */
  .card--front {
    display: flex; flex-direction: column; align-items: center; justify-content: center;
  }
  .front-name {
    font-family: 'Oswald', sans-serif; font-weight: 400;
    color: var(--silver); font-size: 30px; letter-spacing: 1px;
    text-transform: uppercase; text-align: center; line-height: 1.15;
  }
  .front-rule { width: 400px; height: 1px; background: var(--rule); margin: 22px 0 12px; }
  .tagline {
    font-family: 'Open Sans', sans-serif; color: var(--text-light);
    font-size: 13px; letter-spacing: .6px; text-transform: uppercase;
  }
  .front-rule--lower { margin: 12px 0 0; }
</style>
</head>
<body>
<main class="stage">

  <section class="card card--contact" aria-label="Business card, contact side">
    <div class="brand-block">
      <span class="brand-dot"></span>
      <span class="brand-name">Harbourline<br>Growth<br>Advisory</span>
    </div>
    <div class="divider"></div>
    <div class="contact">
      <p class="person">Desmond R Akerly</p>
      <p class="role">Managing Director</p>
      <ul>
        <li><svg viewBox="0 0 12 12"><path d="M2 1h3l1 3-1.5 1a6 6 0 0 0 2.5 2.5L8 6l3 1v3c0 .6-.4 1-1 1A9 9 0 0 1 1 2c0-.6.4-1 1-1z"/></svg>044-555 018 240</li>
        <li><svg viewBox="0 0 12 12"><path d="M3.5 0h5c.6 0 1 .4 1 1v10c0 .6-.4 1-1 1h-5c-.6 0-1-.4-1-1V1c0-.6.4-1 1-1zm.5 1.5v8h4v-8z"/></svg>044-555 018 241</li>
        <li><svg viewBox="0 0 12 12"><path d="M0 2h12v8H0zm1 1v.4l5 3.2 5-3.2V3z"/></svg>info@harbourline.com</li>
        <li><svg viewBox="0 0 12 12"><circle cx="6" cy="6" r="5.5"/></svg>www.harbourline.com</li>
      </ul>
      <p class="address">48 Quayside Row, Harbour Street<br>Portmere Bay, 402190.</p>
    </div>
  </section>

  <section class="card card--front" aria-label="Business card, front side">
    <p class="front-name">Harbourline Growth Advisory</p>
    <div class="front-rule"></div>
    <p class="tagline">Improving Business Profitibility</p>
    <div class="front-rule front-rule--lower"></div>
  </section>

</main>
</body>
</html>
```